Flyer for the Radiant Harvest Worship Day

I am looking to create a flyer for a one day prayer retreat our church is organizing.
This flyer will be posted on social media, websites and will also be printed so it can be mailed to people.
I am looking for something professional, with good use of our logo and band colors (logo colors).
I am counting on the designer's skill, creativity, art and knowledge of media communication to produce a flyer that will effectively and quickly convey the message we are trying to spread.
CONTENT OF THE FLYER:
Event title: Radiant Harvest Worship Day
Date: Tuesday July 2nd, 2019
Time: 11:00AM - 7:00PM
Belmora Hotel, 4875 Wexley Avenue, Portland, Maine 04102 (Room: Juniper)
Event Key words to highlight what the event is about: Prayer, Sharing the Word, Panel discussion, prophecy, Impartation.
Key phrases:
A one day prayer retreat.
Jesus Chris is Lord
Contact info:
www.tolvex.org
Phone: 207 555 3184
Email: contact@brookhavenfold.org

```html
<!DOCTYPE html>
<html lang="en">
<head>
<meta charset="utf-8">
<title>Radiant Harvest Worship Day</title>
<link href="https://fonts.googleapis.com/css2?family=Arimo:wght@400;700&display=swap" rel="stylesheet">
<style>
  :root {
    --navy: #003a5d;
    --orange: #f7931e;
    --gold: #d9b04a;
    --gold-light: #f4dc8a;
    --cream: #fff6c7;
    --yellow: #ffe500;
    --icon-ink: #7a5a00;
    --white: #ffffff;
    --frame: #8a8a8a;
  }
  * { margin: 0; padding: 0; box-sizing: border-box; }
  html, body { width: 900px; height: 1200px; overflow: hidden; background: var(--white); }
  body { font-family: "Arimo", Arial, sans-serif; position: relative; }
  .sheet-edge { position: absolute; inset: 0; border: 1px solid #555; }
  .flyer {
    position: absolute; left: 57px; top: 44px; width: 786px; height: 1110px;
    border: 1px solid var(--frame); overflow: hidden; background: var(--navy);
  }
  .backdrop { position: absolute; left: 0; top: 0; width: 786px; height: 1110px; }
  .brand {
    position: absolute; left: 53px; top: 0; width: 227px; height: 226px;
    background: var(--navy); display: flex; align-items: center; justify-content: center; gap: 12px;
  }
  .brand-mark { width: 16px; height: 16px; background: var(--white); }
  .brand-name { color: var(--white); font-weight: 700; font-size: 40px; line-height: 1; }
  .event-title { position: absolute; left: 334px; top: 58px; font-weight: 700; line-height: 1; }
  .event-title .line-one { display: block; color: var(--navy); font-size: 36px; }
  .event-title .line-two { display: block; color: var(--orange); font-size: 50px; margin-top: 8px; }
  .tagline {
    position: absolute; left: 102px; top: 642px; color: var(--white);
    font-weight: 700; font-size: 25px;
  }
  .declaration {
    position: absolute; left: 102px; top: 700px; color: var(--cream);
    font-weight: 700; font-size: 46px;
  }
  .details { position: absolute; left: 50px; top: 785px; list-style: none; color: var(--white); }
  .details li { display: flex; align-items: flex-start; font-size: 23px; line-height: 35px; }
  .details li + li { margin-top: 26px; }
  .details svg { flex: none; width: 28px; height: 28px; margin: 4px 20px 0 0; }
  .keywords {
    position: absolute; left: 560px; top: 788px; width: 200px; list-style: none;
    border-left: 3px solid var(--gold); padding-left: 16px;
  }
  .keywords li { color: var(--white); font-size: 18px; line-height: 28px; }
  .contact-band {
    position: absolute; left: 0; top: 1008px; width: 786px; height: 102px;
    background: var(--orange); color: var(--white); text-align: center;
  }
  .contact-main {
    display: flex; justify-content: center; align-items: center; gap: 12px;
    font-size: 40px; margin-top: 8px; line-height: 46px;
  }
  .contact-main svg { width: 30px; height: 30px; }
  .contact-email {
    display: flex; justify-content: center; align-items: center; gap: 10px;
    font-size: 26px; margin-top: 4px;
  }
  .contact-email svg { width: 24px; height: 18px; }
</style>
</head>
<body>
<div class="sheet-edge"></div>
<main class="flyer">
  <svg class="backdrop" viewBox="0 0 786 1110">
    <defs>
      <linearGradient id="photoTone" x1="0" y1="0" x2="1" y2="1">
        <stop offset="0" stop-color="#f1f2f3"/>
        <stop offset="0.35" stop-color="#d8cbbf"/>
        <stop offset="0.6" stop-color="#8ea89a"/>
        <stop offset="1" stop-color="#5b6676"/>
      </linearGradient>
      <linearGradient id="topLight" x1="0" y1="0" x2="0" y2="1">
        <stop offset="0" stop-color="#f7f7f8"/>
        <stop offset="1" stop-color="#eceeef"/>
      </linearGradient>
      <linearGradient id="goldSweep" x1="0" y1="1" x2="1" y2="0">
        <stop offset="0" stop-color="#d9b04a"/>
        <stop offset="0.5" stop-color="#f4dc8a"/>
        <stop offset="1" stop-color="#d9b04a"/>
      </linearGradient>
    </defs>
    <rect x="0" y="0" width="786" height="620" fill="url(#topLight)"/>
    <rect x="0" y="226" width="786" height="394" fill="url(#photoTone)" role="img"
          aria-label="Photo of four people standing in a circle with hands on shoulders, heads bowed in prayer"/>
    <path d="M0 515 C150 565 300 575 450 540 C600 500 720 400 786 258 L786 300 C720 430 600 525 450 560 C300 592 140 585 0 535 Z" fill="url(#goldSweep)"/>
    <path d="M0 535 C140 585 300 592 450 560 C600 525 720 430 786 300 L786 1110 L0 1110 Z" fill="#003a5d"/>
  </svg>

  <div class="brand">
    <span class="brand-mark"></span>
    <span class="brand-name">TOLVEX</span>
  </div>

  <h1 class="event-title">
    <span class="line-one">RADIANT HARVEST</span>
    <span class="line-two">WORSHIP DAY</span>
  </h1>

  <p class="tagline">A one day prayer retreat.</p>
  <p class="declaration">Jesus Chris is Lord</p>

  <ul class="details">
    <li>
      <svg viewBox="0 0 28 28"><circle cx="14" cy="14" r="13" fill="var(--yellow)"/><rect x="8" y="9" width="12" height="11" fill="none" stroke="var(--icon-ink)" stroke-width="1.5"/><line x1="8" y1="12.5" x2="20" y2="12.5" stroke="var(--icon-ink)" stroke-width="1.5"/><line x1="11" y1="7" x2="11" y2="10" stroke="var(--icon-ink)" stroke-width="1.5"/><line x1="17" y1="7" x2="17" y2="10" stroke="var(--icon-ink)" stroke-width="1.5"/></svg>
      <span>Date: Tuesday July 2nd, 2019</span>
    </li>
    <li>
      <svg viewBox="0 0 28 28"><circle cx="14" cy="14" r="13" fill="var(--yellow)"/><circle cx="14" cy="14" r="7" fill="none" stroke="var(--icon-ink)" stroke-width="1.5"/><path d="M14 10 V14 L17 16" fill="none" stroke="var(--icon-ink)" stroke-width="1.5"/></svg>
      <span>Time: 11:00AM - 7:00PM</span>
    </li>
    <li>
      <svg viewBox="0 0 28 28"><circle cx="14" cy="14" r="13" fill="var(--yellow)"/><path d="M14 21 C10 16 9 14 9 12 A5 5 0 0 1 19 12 C19 14 18 16 14 21 Z" fill="none" stroke="var(--icon-ink)" stroke-width="1.5"/><circle cx="14" cy="12" r="1.8" fill="var(--icon-ink)"/></svg>
      <span>Belmora Hotel, 4875 Wexley Avenue,<br>Portland, Maine 04102 (Room: Juniper)</span>
    </li>
  </ul>

  <ul class="keywords">
    <li>Prayer</li>
    <li>Sharing the Word</li>
    <li>Panel discussion</li>
    <li>Prophecy</li>
    <li>Impartation</li>
  </ul>

  <footer class="contact-band">
    <div class="contact-main">
      <svg viewBox="0 0 30 30"><g fill="none" stroke="var(--white)" stroke-width="1.6"><circle cx="15" cy="15" r="12"/><ellipse cx="15" cy="15" rx="5" ry="12"/><line x1="3" y1="15" x2="27" y2="15"/><path d="M5 9 H25 M5 21 H25"/></g></svg>
      <span>tolvex.org</span>
      <svg viewBox="0 0 30 30"><path d="M4 12 C4 7 26 7 26 12 L22 14 L20 11 H10 L8 14 Z M9 14 H21 L24 23 H6 Z" fill="none" stroke="var(--white)" stroke-width="1.6"/><circle cx="15" cy="18" r="2.5" fill="none" stroke="var(--white)" stroke-width="1.4"/></svg>
      <span>207 555 3184</span>
    </div>
    <div class="contact-email">
      <svg viewBox="0 0 24 18"><rect x="1" y="1" width="22" height="16" fill="none" stroke="var(--white)" stroke-width="1.4"/><path d="M1 1 L12 10 L23 1" fill="none" stroke="var(--white)" stroke-width="1.4"/></svg>
      <span>contact@brookhavenfold.org</span>
    </div>
  </footer>
</main>
</body>
</html>
```